A start-up named "lumerova" - a clinical research organization needs a new PowerPoint design

We need a new PowerPoint Design (incl. business card and stationery design) for an early-stage start-up named "lumerova" seeking to build an ecosystem/ strategic partner alliances or consortium of committed and active collaborators to guide important components of the clinical trial.

Our ultimate goal is to avoid false neutrals – therapies that have not been and may never be evaluated in clinical trials due to the costs and/ or complexity.

The final design should highlight our patient-centric approach, innovative study design supported with the novel AI platform to make a stronger impact on patient lives.

Please see the attached brief for more details.
Updates

Requesting the proposals on color-coding, business-card designs, clinical research visuals, and icons as well as stationery design.

Target Market(s)

Pharma/ Biotech Executives
Medical Institutions
Clinical Trial Participants (Patients)

Colors
e34398

Requirements
Must have
• Use the Color Version of purple/ magenta logo

```html
<!DOCTYPE html>
<html lang="en">
<head>
<meta charset="utf-8">
<title>lumerova – presentation template</title>
<link rel="stylesheet" href="https://fonts.googleapis.com/css2?family=Poppins:wght@400;500;600;700&family=Open+Sans:wght@400;600&display=swap">
<style>
:root{
  --magenta:#dc2d8a;
  --magenta-deep:#b81a72;
  --magenta-soft:#f3c2dc;
  --ink:#2b2b2b;
  --grey:#777;
  --line:#e4e4e4;
  --paper:#ffffff;
  --bg:#f1f1f3;
  --c1:#e32d91;--c2:#c830cc;--c3:#4ea6dc;--c4:#4775e7;--c5:#8971e1;--c6:#d54773;
}
*{box-sizing:border-box;margin:0;padding:0}
html,body{width:1200px;height:4751px;overflow:hidden;background:var(--bg)}
body{position:relative;font-family:"Open Sans",sans-serif;color:var(--ink)}
.slide{position:absolute;width:558px;height:314px;background:var(--paper);overflow:hidden;box-shadow:0 2px 6px rgba(0,0,0,.08)}
.abs{position:absolute}
.ph{position:absolute}
.logo{font-family:"Poppins",sans-serif;font-weight:700;color:var(--magenta);letter-spacing:-.5px;white-space:nowrap;display:inline-flex;align-items:center;gap:4px}
.logo i{display:inline-block;background:currentColor}
.logo.white{color:#fff}
.mini-logo{position:absolute;right:16px;top:14px;font-size:15px}
.mini-logo i{width:6px;height:6px}
.hd{position:absolute;left:22px;top:20px;font:600 17px "Poppins",sans-serif;color:var(--ink);text-transform:uppercase}
.hd b{color:var(--magenta);font-weight:600}
.hd::after{content:"";position:absolute;left:0;top:26px;width:34px;height:2px;background:var(--magenta)}
.ft{position:absolute;left:0;right:0;bottom:0;height:3px;background:var(--magenta)}
.nav{position:absolute;right:12px;bottom:9px;display:flex;gap:4px}
.nav span{width:9px;height:9px;border:1px solid #bbb;border-radius:50%}
.small{font-size:7px;line-height:1.35;color:var(--grey)}
.tiny{font-size:6px;line-height:1.35;color:var(--grey)}
.ttl{font:600 8.5px "Poppins",sans-serif;color:var(--ink)}
.sub{font:500 6px "Poppins",sans-serif;letter-spacing:3px;color:var(--grey);text-transform:uppercase}
.big-title{font:600 17px "Poppins",sans-serif;text-transform:uppercase;color:var(--ink)}
.pill{position:absolute;background:var(--magenta);color:#fff;font:500 6px "Poppins",sans-serif;text-align:center;border-radius:3px;display:flex;align-items:center;justify-content:center;padding:0 6px}
.icon-circ{position:absolute;border-radius:50%;background:var(--magenta);display:flex;align-items:center;justify-content:center}
.icon-circ.dark{background:#222}
.card{position:absolute;background:#fff;border-radius:6px;box-shadow:0 2px 6px rgba(0,0,0,.15)}
.num{font:700 40px "Poppins",sans-serif;color:#222}
</style>
</head>
<body>

<!-- ===== Booklet presentation (flattened) ===== -->
<section class="booklet">
  <!-- cover -->
  <div class="slide" style="left:560px;top:80px;width:600px;height:338px">
    <svg class="ph" width="600" height="338" viewBox="0 0 600 338">
      <defs><linearGradient id="photoA" x1="0" y1="0" x2="1" y2="1"><stop offset="0" stop-color="#cfe0e6"/><stop offset="1" stop-color="#8aa9b6"/></linearGradient></defs>
      <rect width="600" height="338" fill="var(--magenta-deep)"/>
      <path d="M250 0 H600 V338 H380 C300 250 300 90 250 0Z" fill="var(--magenta)"/>
      <path d="M290 0 H600 V300 C470 300 360 220 340 120 C330 60 310 20 290 0Z" fill="url(#photoA)" role="img" aria-label="Photo of a stethoscope resting beside a laptop"/>
      <path d="M0 250 C180 330 380 300 600 230 V338 H0Z" fill="#fff"/>
    </svg>
    <span class="logo white abs" style="left:36px;top:80px;font-size:24px"><span>lumerova</span><i style="width:9px;height:9px"></i></span>
    <div class="abs big-title" style="left:36px;top:278px;color:var(--magenta);font-size:15px">lumerova template</div>
    <div class="abs sub" style="left:36px;top:302px">subtitle goes here</div>
  </div>
  <!-- open spread -->
  <div class="slide" style="left:40px;top:470px;width:1000px;height:430px">
    <div class="abs" style="left:0;top:0;width:500px;height:430px;border-right:1px solid var(--line)">
      <div class="hd" style="left:34px;top:30px"><b>Our</b> Organization</div>
      <div class="ph" role="img" aria-label="Photo of a hospital corridor with medical staff" style="left:0;top:110px;width:230px;height:200px;background:linear-gradient(135deg,#e9eef2,#9fb3c0)"></div>
      <div class="abs" style="left:230px;top:110px;width:270px;height:200px;background:var(--magenta)">
        <div class="abs" style="left:30px;top:20px;border:1px solid #fff;color:#fff;font:500 13px Poppins,sans-serif;padding:5px 16px">ADD YOUR TITLE HERE</div>
        <p class="abs small" style="left:20px;top:70px;width:230px;color:#fff">Get a clean and modern deck that is designed with care. Easy to change colours, photos and text. You can impress your audience with ease.</p>
      </div>
    </div>
    <div class="abs" style="left:500px;top:0;width:500px;height:430px">
      <div class="hd" style="left:34px;top:30px"><b>Our</b> Services</div>
      <div class="ph" role="img" aria-label="Photo of a doctor with a mother and child" style="left:0;top:80px;width:230px;height:300px;background:linear-gradient(135deg,#eef3f6,#b8c7d2)"></div>
      <div class="icon-circ" style="left:212px;top:110px;width:34px;height:34px"></div>
      <div class="icon-circ dark" style="left:212px;top:170px;width:34px;height:34px"></div>
      <div class="icon-circ" style="left:212px;top:230px;width:34px;height:34px"></div>
      <div class="icon-circ dark" style="left:212px;top:290px;width:34px;height:34px"></div>
      <div class="abs" style="left:262px;top:112px;width:210px"><div class="ttl" style="color:var(--magenta)">Content Title here</div><p class="tiny">A modern deck that is easy to edit.</p></div>
      <div class="abs" style="left:262px;top:172px;width:210px"><div class="ttl">Content Title here</div><p class="tiny">A modern deck that is easy to edit.</p></div>
      <div class="abs" style="left:262px;top:232px;width:210px"><div class="ttl" style="color:var(--magenta)">Content Title here</div><p class="tiny">A modern deck that is easy to edit.</p></div>
      <div class="abs" style="left:262px;top:292px;width:210px"><div class="ttl">Content Title here</div><p class="tiny">A modern deck that is easy to edit.</p></div>
      <span class="logo abs" style="right:30px;bottom:24px;font-size:15px"><span>lumerova</span><i style="width:6px;height:6px"></i></span>
    </div>
  </div>
</section>

<!-- ===== Slide grid ===== -->

<!-- 1 logo white -->
<div class="slide" style="left:28px;top:977px">
  <div class="ph" role="img" aria-label="Faint grey square pattern decoration" style="left:0;top:0;width:260px;height:314px;background:linear-gradient(120deg,#f3f3f3,#fff 70%)"></div>
  <span class="logo abs" style="left:176px;top:132px;font-size:36px"><span>lumerova</span><i style="width:12px;height:12px"></i></span>
  <div class="abs tiny" style="right:6px;top:150px;transform:rotate(90deg);transform-origin:right top;letter-spacing:2px">WWW.WEBSITE.COM</div>
</div>

<!-- 2 logo magenta -->
<div class="slide" style="left:614px;top:977px;background:var(--magenta)">
  <div class="ph" role="img" aria-label="Tonal square pattern background" style="inset:0;background:linear-gradient(135deg,var(--magenta),var(--magenta-deep))"></div>
  <span class="logo white abs" style="left:176px;top:132px;font-size:36px"><span>lumerova</span><i style="width:12px;height:12px"></i></span>
</div>

<!-- 3 cover -->
<div class="slide" style="left:28px;top:1318px">
  <svg class="ph" width="558" height="314" viewBox="0 0 558 314">
    <defs><linearGradient id="photoB" x1="0" y1="0" x2="1" y2="1"><stop offset="0" stop-color="#d6e5ea"/><stop offset="1" stop-color="#8aa7b4"/></linearGradient></defs>
    <rect width="558" height="314" fill="var(--magenta-deep)"/>
    <path d="M240 0 H558 V230 C440 250 350 220 320 150 C300 90 270 30 240 0Z" fill="var(--magenta)"/>
    <path d="M280 0 H558 V200 C460 215 380 180 360 120 C345 70 315 20 280 0Z" fill="url(#photoB)" role="img" aria-label="Photo of a stethoscope beside a laptop"/>
    <path d="M0 200 C150 250 380 260 558 220 V314 H0Z" fill="#fff"/>
  </svg>
  <span class="logo white abs" style="left:36px;top:92px;font-size:21px"><span>lumerova</span><i style="width:8px;height:8px"></i></span>
  <div class="abs big-title" style="left:34px;top:250px;font-size:15px"><span style="color:var(--magenta)">lumerova</span> template</div>
  <div class="abs sub" style="left:36px;top:276px">subtitle goes here</div>
  <div class="abs" style="right:22px;top:276px;display:flex;gap:3px"><span style="width:9px;height:9px;border:1px solid #555;border-radius:50%"></span><span style="width:9px;height:9px;border:1px solid #555;border-radius:50%"></span><span style="width:9px;height:9px;border:1px solid #555;border-radius:50%"></span><span style="width:9px;height:9px;border:1px solid #555;border-radius:50%"></span></div>
</div>

<!-- 4 photo title -->
<div class="slide" style="left:614px;top:1318px">
  <div class="ph" role="img" aria-label="Photo of a smiling doctor with a mother and daughter" style="inset:0;background:linear-gradient(100deg,#d9e3ea,#f6f8fa 70%)"></div>
  <span class="logo abs" style="right:28px;top:44px;font-size:30px"><span>lumerova</span><i style="width:10px;height:10px"></i></span>
  <div class="abs num" style="right:38px;top:160px;font-size:60px;line-height:1">01</div>
  <div class="abs" style="right:38px;top:238px;font:600 15px Poppins,sans-serif">ADD YOUR TITLE HERE</div>
  <div class="abs sub" style="right:38px;top:260px">subtitle goes here</div>
</div>

<!-- 5 lab photo -->
<div class="slide" style="left:28px;top:1659px">
  <div class="ph" role="img" aria-label="Photo of laboratory glassware in blue and pink light" style="inset:12px;background:linear-gradient(135deg,#1d6fb4,#3fa6e0 50%,#7b4aa8)"></div>
  <svg class="ph" width="558" height="314" viewBox="0 0 558 314"><g fill="none" stroke="#fff" stroke-width="3"><rect x="230" y="12" width="74" height="70"/><rect x="304" y="12" width="74" height="70"/><rect x="378" y="12" width="80" height="70"/><rect x="458" y="12" width="88" height="70"/><rect x="230" y="82" width="74" height="220"/><rect x="304" y="82" width="154" height="220"/><rect x="458" y="82" width="88" height="220"/></g></svg>
  <span class="logo white abs" style="left:40px;top:140px;font-size:27px"><span>lumerova</span><i style="width:9px;height:9px"></i></span>
</div>

<!-- 6 master white -->
<div class="slide" style="left:614px;top:1659px">
  <span class="logo abs" style="left:36px;top:56px;font-size:27px"><span>lumerova</span><i style="width:9px;height:9px"></i></span>
  <div class="abs" style="left:38px;top:208px;width:16px;height:16px;background:var(--magenta)"></div>
  <div class="abs" style="left:38px;top:232px;font:600 15px Poppins,sans-serif">MASTER SLIDE TEMPLATE</div>
  <div class="abs sub" style="left:38px;top:256px">subtitle goes here</div>
  <div class="ph" role="img" aria-label="Mosaic of square laboratory and research photos" style="left:240px;top:12px;width:300px;height:290px">
    <div class="abs" style="left:100px;top:70px;width:80px;height:80px;border-radius:8px;background:linear-gradient(135deg,#eef3f6,#b9cad6)"></div>
    <div class="abs" style="left:190px;top:20px;width:40px;height:40px;border-radius:6px;background:linear-gradient(135deg,#e0eaf0,#97b3c6)"></div>
    <div class="abs" style="left:240px;top:100px;width:50px;height:50px;border-radius:6px;background:linear-gradient(135deg,#cde0ee,#6fa3cc)"></div>
    <div class="abs" style="left:180px;top:160px;width:70px;height:70px;border-radius:8px;background:linear-gradient(135deg,#e8eff4,#a9bdcc)"></div>
    <div class="abs" style="left:110px;top:170px;width:56px;height:56px;border-radius:6px;background:linear-gradient(135deg,#eef4ea,#9fc49a)"></div>
    <div class="abs" style="left:60px;top:50px;width:30px;height:30px;border-radius:4px;background:#dde6ec"></div>
  </div>
</div>

<!-- 7 master magenta -->
<div class="slide" style="left:28px;top:2000px;background:var(--magenta)">
  <span class="logo white abs" style="left:36px;top:56px;font-size:27px"><span>lumerova</span><i style="width:9px;height:9px"></i></span>
  <div class="abs" style="left:38px;top:210px;width:16px;height:16px;background:#fff"></div>
  <div class="abs" style="left:38px;top:232px;font:600 15px Poppins,sans-serif;color:#fff">MASTER SLIDE TEMPLATE</div>
  <div class="abs sub" style="left:38px;top:256px;color:#fde">subtitle goes here</div>
  <div class="ph" role="img" aria-label="Mosaic of square research photos in grey tones" style="left:240px;top:12px;width:300px;height:290px">
    <div class="abs" style="left:40px;top:90px;width:90px;height:80px;border-radius:8px;background:linear-gradient(135deg,#fafafa,#bbb)"></div>
    <div class="abs" style="left:130px;top:20px;width:60px;height:60px;border-radius:6px;background:linear-gradient(135deg,#f1f1f1,#aaa)"></div>
    <div class="abs" style="left:190px;top:60px;width:60px;height:60px;border-radius:6px;background:linear-gradient(135deg,#eee,#999)"></div>
    <div class="abs" style="left:160px;top:150px;width:80px;height:80px;border-radius:8px;background:linear-gradient(135deg,#f4f4f4,#b0b0b0)"></div>
    <div class="abs" style="left:250px;top:190px;width:40px;height:40px;border-radius:6px;background:#ddd"></div>
  </div>
</div>

<!-- 8 agenda -->
<div class="slide" style="left:614px;top:2000px">
  <div class="hd"><b>Our</b> Agenda</div>
  <span class="logo mini-logo"><span>lumerova</span><i></i></span>
  <div class="ph" role="img" aria-label="Faint grey square pattern decoration" style="left:20px;top:130px;width:170px;height:150px;background:linear-gradient(135deg,#f4f4f4,#fff)"></div>
  <div class="abs" style="left:318px;top:60px;width:180px">
    <div class="ttl">Agenda Text 1</div><p class="tiny">A simple placeholder line for the printing and layout work.</p>
    <div class="ttl" style="margin-top:16px">Agenda Text 2</div><p class="tiny">A simple placeholder line for the printing and layout work.</p>
    <div class="ttl" style="margin-top:16px">Agenda Text 3</div><p class="tiny">A simple placeholder line for the printing and layout work.</p>
    <div class="ttl" style="margin-top:16px">Agenda Text 4</div><p class="tiny">A simple placeholder line for the printing and layout work.</p>
  </div>
  <div class="ft"></div><div class="nav"><span></span><span></span></div>
</div>

<!-- 9 process 1 -->
<div class="slide" style="left:28px;top:2341px">
  <div class="hd"><b>New drug</b> development process<sup style="font-size:8px">1</sup></div>
  <span class="logo mini-logo"><span>lumerova</span><i></i></span>
  <svg class="ph" width="558" height="314" viewBox="0 0 558 314">
    <line x1="40" y1="130" x2="510" y2="130" stroke="#d9d9d9" stroke-width="3"/>
    <polygon points="510,124 522,130 510,136" fill="#d9d9d9"/>
    <g fill="#fff" stroke="var(--magenta)" stroke-width="5">
      <circle cx="84" cy="130" r="28"/><circle cx="180" cy="130" r="28"/><circle cx="276" cy="130" r="28"/><circle cx="372" cy="130" r="28"/><circle cx="468" cy="130" r="28"/>
    </g>
    <g fill="none" stroke="var(--magenta)" stroke-width="2">
      <rect x="75" y="121" width="18" height="18" rx="3"/><circle cx="84" cy="130" r="4"/>
      <path d="M176 119 v8 l-7 12 h22 l-7-12 v-8"/>
      <path d="M268 140 l14-20 M272 124 l8 8"/>
      <path d="M362 140 c4-14 16-20 22-20 c0 8-6 20-22 20z"/>
      <rect x="460" y="121" width="6" height="18" rx="3"/><rect x="470" y="121" width="6" height="18" rx="3"/>
    </g>
  </svg>
  <div class="card" style="left:48px;top:176px;width:72px;height:56px"><p class="tiny" style="text-align:center;padding:8px 4px">Lorem text is a simple dummy line here</p></div>
  <div class="card" style="left:144px;top:176px;width:72px;height:56px"><p class="tiny" style="text-align:center;padding:8px 4px">Lorem text is a simple dummy line here</p></div>
  <div class="card" style="left:240px;top:176px;width:72px;height:56px"><p class="tiny" style="text-align:center;padding:8px 4px">Lorem text is a simple dummy line here</p></div>
  <div class="card" style="left:336px;top:176px;width:72px;height:56px"><p class="tiny" style="text-align:center;padding:8px 4px">Lorem text is a simple dummy line here</p></div>
  <div class="card" style="left:432px;top:176px;width:72px;height:56px"><p class="tiny" style="text-align:center;padding:8px 4px">Lorem text is a simple dummy line here</p></div>
  <div class="ft"></div><div class="nav"><span></span><span></span></div>
</div>

<!-- 10 process 2 -->
<div class="slide" style="left:614px;top:2341px">
  <div class="hd"><b>New drug</b> development process<sup style="font-size:8px">2</sup></div>
  <span class="logo mini-logo"><span>lumerova</span><i></i></span>
  <div class="abs num" style="left:24px;top:78px;font-size:38px">70</div>
  <div class="abs num" style="left:24px;top:144px;font-size:38px">67</div>
  <div class="abs num" style="left:24px;top:212px;font-size:38px">30</div>
  <div class="icon-circ" style="left:68px;top:78px;width:18px;height:18px;color:#fff;font:600 9px Poppins,sans-serif">%</div>
  <div class="icon-circ" style="left:68px;top:144px;width:18px;height:18px;color:#fff;font:600 9px Poppins,sans-serif">%</div>
  <div class="icon-circ" style="left:68px;top:212px;width:18px;height:18px;color:#fff;font:600 9px Poppins,sans-serif">%</div>
  <div class="pill" style="left:102px;top:84px;width:120px;height:42px">of potential participants live far away from the nearest study centre</div>
  <div class="pill" style="left:102px;top:150px;width:120px;height:42px">of sites fail to meet enrolment goals</div>
  <div class="pill" style="left:102px;top:218px;width:120px;height:42px">average drop-out rate</div>
  <svg class="ph" width="558" height="314" viewBox="0 0 558 314"><polygon points="236,104 274,104 320,170 274,236 236,236 236,104" fill="#d4d4d4"/></svg>
  <div class="card" style="left:336px;top:70px;width:190px;height:200px;background:linear-gradient(135deg,#fff,#eef3f6)">
    <div class="abs num" style="left:40px;top:24px;font-size:64px;line-height:1">85</div>
    <div class="icon-circ" style="left:140px;top:20px;width:30px;height:30px;color:#fff;font:600 14px Poppins,sans-serif">%</div>
    <div class="abs" style="left:20px;top:110px;width:150px;text-align:center;font:600 11px Poppins,sans-serif;line-height:1.3">of clinical trials fail to retain enough patients</div>
  </div>
  <div class="ft"></div><div class="nav"><span></span><span></span></div>
</div>

<!-- 11 enrolment bars -->
<div class="slide" style="left:28px;top:2682px">
  <div class="hd"><b>Why don't</b> patients enroll in trials?</div>
  <span class="logo mini-logo"><span>lumerova</span><i></i></span>
  <svg class="ph" width="558" height="314" viewBox="0 0 558 314">
    <line x1="36" y1="70" x2="36" y2="284" stroke="#222" stroke-width="3"/><polygon points="30,72 36,60 42,72" fill="#222"/>
    <line x1="36" y1="284" x2="510" y2="284" stroke="#222" stroke-width="3"/><polygon points="508,278 520,284 508,290" fill="#222"/>
    <g fill="#f5f5f5"><rect x="60" y="84" width="136" height="198"/><rect x="208" y="84" width="136" height="198"/><rect x="356" y="84" width="136" height="198"/></g>
    <g fill="var(--magenta)"><rect x="60" y="72" width="136" height="18" rx="2"/><rect x="208" y="72" width="136" height="18" rx="2"/><rect x="356" y="72" width="136" height="18" rx="2"/>
    <rect x="82" y="164" width="92" height="118"/><rect x="230" y="166" width="92" height="116"/><rect x="378" y="194" width="92" height="88"/></g>
    <g fill="none" stroke="#fff" stroke-width="1.5"><circle cx="128" cy="256" r="13"/><circle cx="276" cy="256" r="13"/><circle cx="424" cy="256" r="13"/></g>
  </svg>
  <div class="abs" style="left:60px;top:75px;width:136px;text-align:center;color:#fff;font:600 7px Poppins,sans-serif">TRUST</div>
  <div class="abs" style="left:208px;top:75px;width:136px;text-align:center;color:#fff;font:600 7px Poppins,sans-serif">UNDERSTANDING</div>
  <div class="abs" style="left:356px;top:75px;width:136px;text-align:center;color:#fff;font:600 7px Poppins,sans-serif">CONVENIENCE</div>
  <div class="card" style="left:100px;top:130px;width:44px;height:22px;text-align:center;font:600 12px Poppins,sans-serif;line-height:22px">67%</div>
  <div class="card" style="left:248px;top:134px;width:44px;height:22px;text-align:center;font:600 12px Poppins,sans-serif;line-height:22px">66%</div>
  <div class="card" style="left:396px;top:162px;width:44px;height:22px;text-align:center;font:600 12px Poppins,sans-serif;line-height:22px">56%</div>
  <div class="abs tiny" style="left:82px;top:216px;width:92px;text-align:center;color:#fff">add your text here</div>
  <div class="abs tiny" style="left:230px;top:216px;width:92px;text-align:center;color:#fff">add your text here</div>
  <div class="abs tiny" style="left:378px;top:216px;width:92px;text-align:center;color:#fff">add your text here</div>
  <div class="abs tiny" style="left:10px;top:200px;transform:rotate(-90deg);transform-origin:left top">add your text here</div>
  <div class="ft"></div><div class="nav"><span></span><span></span></div>
</div>

<!-- 12 organization -->
<div class="slide" style="left:614px;top:2682px">
  <div class="hd"><b>Our</b> Organization</div>
  <span class="logo mini-logo"><span>lumerova</span><i></i></span>
  <div class="ph" role="img" aria-label="Photo of a bright hospital corridor with medical staff" style="left:0;top:70px;width:280px;height:196px;background:linear-gradient(135deg,#f0f4f6,#a7b9c5)"></div>
  <div class="abs" style="left:280px;top:70px;width:278px;height:196px;background:var(--magenta)">
    <div class="abs" style="left:38px;top:14px;border:1px solid #fff;color:#fff;font:500 13px Poppins,sans-serif;padding:4px 18px">ADD YOUR TITLE HERE</div>
    <p class="abs tiny" style="left:18px;top:54px;width:244px;color:#fff">Get a clean and modern deck that is designed with care. Easy to change colours, photos and text. You can simply impress your audience and add a unique zing to your talk. A clean deck that is easy to edit.</p>
    <p class="abs tiny" style="left:18px;top:128px;width:244px;color:#fff">Get a clean and modern deck that is designed with care. Easy to change colours, photos and text. You can impress your audience with ease.</p>
  </div>
  <div class="ft"></div><div class="nav"><span></span><span></span></div>
</div>

<!-- 13 vision -->
<div class="slide" style="left:28px;top:3023px">
  <div class="hd"><b>Our</b> Vision</div>
  <span class="logo mini-logo"><span>lumerova</span><i></i></span>
  <div class="abs" style="left:0;top:70px;width:558px;height:196px;background:linear-gradient(90deg,var(--magenta),#e45aa6)">
    <div class="abs" style="left:176px;top:18px;border:1px solid #fff;color:#fff;font:500 13px Poppins,sans-serif;padding:4px 18px">ADD YOUR TITLE HERE</div>
    <p class="abs tiny" style="left:40px;top:70px;width:480px;color:#fff">Get a clean and modern deck that is designed with care. Easy to change colours, photos and text. You can simply impress your audience and add a unique zing and appeal to your presentations. A clean deck that is easy to edit and share with your team.</p>
  </div>
  <div class="ft"></div><div class="nav"><span></span><span></span></div>
</div>

<!-- 14 services -->
<div class="slide" style="left:614px;top:3023px">
  <div class="hd"><b>Our</b> Services</div>
  <span class="logo mini-logo"><span>lumerova</span><i></i></span>
  <div class="ph" role="img" aria-label="Photo of a doctor showing a clipboard to a mother and daughter" style="left:0;top:0;width:270px;height:311px;background:linear-gradient(120deg,rgba(255,255,255,0) 20%,#dfe7ec 40%,#b7c7d2)"></div>
  <div class="icon-circ" style="left:246px;top:68px;width:32px;height:32px;border:3px solid #fff"></div>
  <div class="icon-circ dark" style="left:246px;top:126px;width:32px;height:32px;border:3px solid #fff"></div>
  <div class="icon-circ" style="left:246px;top:184px;width:32px;height:32px;border:3px solid #fff"></div>
  <div class="icon-circ dark" style="left:246px;top:242px;width:32px;height:32px;border:3px solid #fff"></div>
  <div class="abs" style="left:292px;top:66px;width:250px"><div class="ttl" style="color:var(--magenta)">Content Title here</div><p class="tiny">Get a clean and modern deck. Easy to change colours, photos and text.</p></div>
  <div class="abs" style="left:292px;top:124px;width:250px"><div class="ttl">Content Title here</div><p class="tiny">Get a clean and modern deck. Easy to change colours, photos and text.</p></div>
  <div class="abs" style="left:292px;top:182px;width:250px"><div class="ttl" style="color:var(--magenta)">Content Title here</div><p class="tiny">Get a clean and modern deck. Easy to change colours, photos and text.</p></div>
  <div class="abs" style="left:292px;top:240px;width:250px"><div class="ttl">Content Title here</div><p class="tiny">Get a clean and modern deck. Easy to change colours, photos and text.</p></div>
  <div class="ft"></div><div class="nav"><span></span><span></span></div>
</div>

<!-- 15 cards -->
<div class="slide" style="left:28px;top:3364px">
  <div class="hd"><b>Add you</b> title here</div>
  <span class="logo mini-logo"><span>lumerova</span><i></i></span>
  <p class="abs tiny" style="left:42px;top:80px;width:190px;text-align:justify">Get a clean and modern deck that is designed with care. Easy to change colours, photos and text.</p>
  <div class="ph" role="img" aria-label="Blue illustration of a DNA double helix" style="left:298px;top:36px;width:248px;height:236px;background:linear-gradient(135deg,#9fc3e3,#3d78b5)"></div>
  <div class="card" style="left:38px;top:158px;width:88px;height:90px;background:var(--magenta)"><div class="ttl" style="color:#fff;text-align:center;margin-top:46px">Content Title</div><p class="tiny" style="color:#fff;text-align:center">A modern deck here</p></div>
  <div class="card" style="left:144px;top:158px;width:88px;height:90px"><div class="ttl" style="text-align:center;margin-top:46px">Content Title</div><p class="tiny" style="text-align:center">A modern deck here</p></div>
  <div class="card" style="left:250px;top:158px;width:88px;height:90px"><div class="ttl" style="text-align:center;margin-top:46px">Content Title</div><p class="tiny" style="text-align:center">A modern deck here</p></div>
  <div class="card" style="left:356px;top:158px;width:88px;height:90px"><div class="ttl" style="text-align:center;margin-top:46px">Content Title</div><p class="tiny" style="text-align:center">A modern deck here</p></div>
  <svg class="ph" width="558" height="314" viewBox="0 0 558 314"><g fill="none" stroke-width="1.8"><path d="M74 190 l14-14 m-8 0 h8 v8" stroke="#fff"/><circle cx="188" cy="184" r="8" stroke="#333"/><path d="M288 194 v-14 h16 v14" stroke="#333"/><path d="M392 196 v-8 m6 8 v-14 m6 14 v-20" stroke="#333"/></g></svg>
  <div class="ft"></div><div class="nav"><span></span><span></span></div>
</div>

<!-- 16 another process -->
<div class="slide" style="left:614px;top:3364px">
  <div class="hd"><b>Another</b> Process</div>
  <span class="logo mini-logo"><span>lumerova</span><i></i></span>
  <div class="ph" role="img" aria-label="Dark hexagonal emblem illustration" style="left:222px;top:100px;width:112px;height:112px;border-radius:50%;background:radial-gradient(#555,#111)"></div>
  <div class="icon-circ" style="left:212px;top:96px;width:26px;height:26px"></div>
  <div class="icon-circ" style="left:318px;top:96px;width:26px;height:26px"></div>
  <div class="icon-circ" style="left:196px;top:144px;width:26px;height:26px"></div>
  <div class="icon-circ" style="left:334px;top:144px;width:26px;height:26px"></div>
  <div class="icon-circ" style="left:212px;top:192px;width:26px;height:26px"></div>
  <div class="icon-circ" style="left:318px;top:192px;width:26px;height:26px"></div>
  <div class="abs" style="left:40px;top:90px;width:160px;text-align:center"><div class="ttl">Content Title</div><p class="tiny">A modern deck that is designed well.</p></div>
  <div class="abs" style="left:24px;top:140px;width:160px;text-align:center"><div class="ttl">Content Title</div><p class="tiny">A modern deck that is designed well.</p></div>
  <div class="abs" style="left:40px;top:190px;width:160px;text-align:center"><div class="ttl">Content Title</div><p class="tiny">A modern deck that is designed well.</p></div>
  <div class="abs" style="left:356px;top:90px;width:160px"><div class="ttl">Content Title</div><p class="tiny">A modern deck that is designed well.</p></div>
  <div class="abs" style="left:372px;top:140px;width:160px"><div class="ttl">Content Title</div><p class="tiny">A modern deck that is designed well.</p></div>
  <div class="abs" style="left:356px;top:190px;width:160px"><div class="ttl">Content Title</div><p class="tiny">A modern deck that is designed well.</p></div>
  <div class="ft"></div><div class="nav"><span></span><span></span></div>
</div>

<!-- 17 section -->
<div class="slide" style="left:28px;top:3705px;background:var(--magenta)">
  <div class="ph" role="img" aria-label="Faded photo of laboratory beakers" style="inset:0;background:linear-gradient(135deg,#e46ab0,var(--magenta) 60%,#c8207d)"></div>
  <span class="logo white abs" style="left:354px;top:180px;font-size:16px"><span>lumerova</span><i style="width:6px;height:6px"></i></span>
  <div class="abs" style="left:354px;top:204px;font:600 19px Poppins,sans-serif;color:#fff">SECTION SLIDE</div>
  <p class="abs tiny" style="left:354px;top:232px;width:150px;color:#fff">A modern deck that is designed with care.</p>
</div>

<!-- 18 chart -->
<div class="slide" style="left:614px;top:3705px">
  <div class="hd"><b>Graphic</b> chart slide</div>
  <span class="logo mini-logo"><span>lumerova</span><i></i></span>
  <svg class="ph" width="558" height="314" viewBox="0 0 558 314">
    <g fill="#f3f5f7"><rect x="28" y="70" width="140" height="200" rx="4"/><rect x="208" y="70" width="140" height="200" rx="4"/><rect x="388" y="70" width="140" height="200" rx="4"/></g>
    <g fill="none" stroke-width="9">
      <circle cx="98" cy="170" r="34" stroke="#eee"/><circle cx="98" cy="170" r="34" stroke="var(--magenta)" stroke-dasharray="145 214" transform="rotate(-90 98 170)"/>
      <circle cx="278" cy="170" r="34" stroke="#eee"/><circle cx="278" cy="170" r="34" stroke="var(--magenta)" stroke-dasharray="75 214" transform="rotate(-90 278 170)"/>
      <circle cx="458" cy="170" r="34" stroke="#eee"/><circle cx="458" cy="170" r="34" stroke="var(--magenta)" stroke-dasharray="118 214" transform="rotate(-90 458 170)"/>
    </g>
    <g font-family="Poppins,sans-serif" font-weight="600" font-size="17" fill="var(--magenta)" text-anchor="middle"><text x="98" y="176">68%</text><text x="278" y="176">35%</text><text x="458" y="176">55%</text></g>
  </svg>
  <div class="abs ttl" style="left:28px;top:80px;width:140px;text-align:center">Content Title<br>Here</div>
  <div class="abs ttl" style="left:208px;top:80px;width:140px;text-align:center">Content Title<br>Here</div>
  <div class="abs ttl" style="left:388px;top:80px;width:140px;text-align:center">Content Title<br>Here</div>
  <p class="abs tiny" style="left:40px;top:218px;width:116px;text-align:center">A clean and modern deck that is designed well.</p>
  <p class="abs tiny" style="left:220px;top:218px;width:116px;text-align:center">A clean and modern deck that is designed well.</p>
  <p class="abs tiny" style="left:400px;top:218px;width:116px;text-align:center">A clean and modern deck that is designed well.</p>
  <div class="ft"></div><div class="nav"><span></span><span></span></div>
</div>

<!-- 19 icons -->
<div class="slide" style="left:28px;top:4046px">
  <div class="hd"><b>Free</b> Icons</div>
  <span class="logo mini-logo"><span>lumerova</span><i></i></span>
  <svg class="ph" x="0" y="0" width="558" height="314" viewBox="0 0 558 314">
    <defs>
      <pattern id="iconGrid" width="88" height="22" patternUnits="userSpaceOnUse">
        <g fill="none" stroke="#444" stroke-width="1">
          <circle cx="8" cy="11" r="6"/>
          <rect x="24" y="5" width="12" height="12" rx="2"/>
          <path d="M46 17 l6-12 l6 12z"/>
          <path d="M68 5 v12 m-6-6 h12"/>
          <path d="M80 15 h6 m-6-4 h6 m-6-4 h6"/>
        </g>
      </pattern>
    </defs>
    <rect x="22" y="64" width="510" height="214" fill="url(#iconGrid)"/>
  </svg>
  <div class="ft"></div><div class="nav"><span></span><span></span></div>
</div>

<!-- 20 colour coding -->
<div class="slide" style="left:614px;top:4046px">
  <div class="abs" style="left:22px;top:20px;font:600 17px Poppins,sans-serif"><span style="color:var(--magenta)">Color</span> Coding</div>
  <span class="logo mini-logo"><span>lumerova</span><i></i></span>
  <div class="abs" style="left:36px;top:72px;width:34px;height:34px;background:var(--c1)"></div>
  <div class="abs" style="left:36px;top:116px;width:34px;height:34px;background:var(--c2)"></div>
  <div class="abs" style="left:36px;top:160px;width:34px;height:34px;background:var(--c3)"></div>
  <div class="abs" style="left:36px;top:204px;width:34px;height:34px;background:var(--c4)"></div>
  <div class="abs" style="left:36px;top:248px;width:34px;height:34px;background:var(--c5)"></div>
  <div class="abs" style="left:196px;top:72px;width:34px;height:34px;background:var(--c6)"></div>
  <div class="abs small" style="left:92px;top:84px;color:#333">RGB – 227,45,145</div>
  <div class="abs small" style="left:92px;top:128px;color:#333">RGB – 200,48,204</div>
  <div class="abs small" style="left:92px;top:172px;color:#333">RGB – 78,166,220</div>
  <div class="abs small" style="left:92px;top:216px;color:#333">RGB – 71,117,231</div>
  <div class="abs small" style="left:92px;top:260px;color:#333">RGB – 137,113,225</div>
  <div class="abs small" style="left:246px;top:84px;color:#333">RGB – 213,71,115</div>
  <svg class="ph" width="558" height="314" viewBox="0 0 558 314">
    <text x="350" y="134" font-size="7" fill="#555" font-family="Open Sans,sans-serif">Chart Title</text>
    <line x1="260" y1="250" x2="500" y2="250" stroke="#ccc"/>
    <g><rect x="270" y="180" width="18" height="70" fill="var(--c1)"/><rect x="288" y="208" width="18" height="42" fill="var(--c2)"/><rect x="306" y="200" width="18" height="50" fill="var(--c4)"/><rect x="324" y="232" width="18" height="18" fill="var(--c5)"/><rect x="342" y="234" width="18" height="16" fill="var(--c3)"/><rect x="360" y="230" width="18" height="20" fill="var(--c4)"/><rect x="378" y="172" width="18" height="78" fill="var(--c6)"/><rect x="396" y="208" width="18" height="42" fill="var(--c2)"/><rect x="414" y="212" width="18" height="38" fill="#4a2a8a"/><rect x="432" y="182" width="18" height="68" fill="var(--c4)"/></g>
    <g><rect x="420" y="60" width="80" height="60" fill="#fff" stroke="#ccc"/><g><rect x="428" y="70" width="64" height="8" fill="var(--c3)"/><rect x="428" y="82" width="64" height="8" fill="var(--c2)"/><rect x="428" y="94" width="64" height="8" fill="var(--c5)"/></g></g>
  </svg>
  <div class="ft"></div><div class="nav"><span></span><span></span></div>
</div>

<!-- 21 thank you -->
<div class="slide" style="left:321px;top:4387px">
  <div class="ph" role="img" aria-label="Faint grey square pattern decoration" style="left:250px;top:0;width:200px;height:160px;background:linear-gradient(135deg,#fff,#f3f3f3)"></div>
  <div class="abs" style="left:48px;top:74px;font:500 19px Poppins,sans-serif">Thank You</div>
  <div class="abs" style="left:52px;top:100px;width:30px;height:2px;background:var(--magenta)"></div>
  <div class="abs" style="left:48px;top:140px;border:1px solid var(--magenta);border-radius:10px;padding:3px 14px;font:600 7px Poppins,sans-serif;letter-spacing:2px;color:var(--magenta)">PRESENTER NAME</div>
  <svg class="ph" width="558" height="314" viewBox="0 0 558 314" fill="var(--magenta)">
    <path d="M58 180 q0-4 3-4 l2 3 -2 2 q2 4 6 6 l2-2 3 2 q0 3-4 3 q-10-2-10-10z"/>
    <rect x="57" y="204" width="10" height="10" rx="2" fill="none" stroke="var(--magenta)" stroke-width="1.5"/><circle cx="62" cy="209" r="2.5" fill="none" stroke="var(--magenta)" stroke-width="1.2"/>
    <path d="M56 230 h12 v9 h-12z"/><path d="M62 254 c-4 0-5 3-5 5 c0 4 5 9 5 9 s5-5 5-9 c0-2-1-5-5-5z"/>
  </svg>
  <div class="abs tiny" style="left:78px;top:180px;color:#333">+1 234 567 890</div>
  <div class="abs tiny" style="left:78px;top:205px;color:#333">www.yourwebsite.com</div>
  <div class="abs tiny" style="left:78px;top:231px;color:#333">addyouremail@here.com</div>
  <div class="abs tiny" style="left:78px;top:257px;color:#333">Add your location here</div>
  <span class="logo abs" style="left:326px;top:148px;font-size:33px"><span>lumerova</span><i style="width:11px;height:11px"></i></span>
</div>

</body>
</html>
```